Website for my photography business

I need a website for my photography business, Bram Kellet Photography. I need a website that has a landing page with a cover photo of each kind of photography I do. For example, Nature, Weddings, Portraits and Architecture. I want it so that when someone comes onto my website they have to choose which kind of photography page they want to visit. So if they click on the wedding photo it will open to a page with my wedding portfolio images and a contact me button. If they choose nature photography I want them to be redirected to an e-commerce section where they can purchase prints. Architecture and Portraits should open up to their respective portfolios with about me and contact info. I like this kind of format because I want people who come to my website for a specific type of photography to be able to be directed there easily without having to look at a mix of other kinds of photography. I will provide a few files to use as placeholders. I have already purchased the bramkelletphotography.example domain name. A Wix website would be great because I am most familiar with it but I am open to anything.

Industry/Entity Type

Photographer

Number of Pages Required

5+ page

Requirements
Must have
• Landing Page and e-commerce

```html
<!DOCTYPE html>
<html lang="en">
<head>
<meta charset="utf-8">
<title>Bram Kellet Photography</title>
<link href="https://fonts.googleapis.com/css2?family=Poppins:wght@300;400&family=Roboto:wght@400;700&family=Open+Sans:wght@400&display=swap" rel="stylesheet">
<style>
  :root {
    --ink: #1a0d0a;
    --accent-brown: #4a1f17;
    --nav-text: #ffffff;
    --footer-bg: #333333;
    --footer-text: #ffffff;
    --page-bg: #ffffff;
    --title-grey: #3d3d3d;
    --star: #f4c21b;
  }
  * { margin: 0; padding: 0; box-sizing: border-box; }
  html, body { width: 1200px; height: 2411px; overflow: hidden; background: var(--page-bg); }
  body { position: relative; font-family: "Poppins", sans-serif; }

  .hero {
    position: absolute; left: 0; top: 0; width: 1200px; height: 642px;
    background:
      linear-gradient(180deg, #4a5fb0 0%, #6a7fc8 14%, #9fb0d9 28%, #d6d2c4 38%, #8fa3d8 48%, #5d74c4 60%, #2f3f88 78%, #1d2a5e 100%);
  }
  .brand {
    position: absolute; left: 112px; top: 62px;
    display: flex; align-items: center; gap: 12px;
    font-family: "Poppins", sans-serif; font-weight: 300; font-size: 30px; color: #2a2f5a;
  }
  .brand-dot { width: 12px; height: 12px; background: var(--star); border-radius: 50%; }
  .main-nav {
    position: absolute; top: 35px; left: 582px; width: 520px; height: 20px;
    font-family: "Poppins", sans-serif; font-size: 13px; color: var(--nav-text);
  }
  .main-nav span { position: absolute; top: 0; white-space: nowrap; }
  .cart { position: absolute; left: 466px; top: -5px; width: 26px; height: 24px; }
  .cart-count { left: 497px; }

  .hero-title {
    position: absolute; top: 230px; left: 0; width: 1200px; text-align: center;
    font-family: "Roboto", sans-serif; font-weight: 700; font-size: 50px; letter-spacing: 0.5px;
    line-height: 60px; color: var(--ink);
  }
  .hero-sub {
    position: absolute; top: 294px; left: 400px; width: 400px; text-align: center;
    font-family: "Roboto", sans-serif; font-size: 17px; line-height: 27px; color: var(--ink);
  }

  .category { position: absolute; width: 438px; }
  .category-num { font-size: 15px; color: var(--accent-brown); height: 31px; line-height: 21px; }
  .category-photo { width: 438px; }
  .category-name {
    text-align: center; font-weight: 300; font-size: 26px; color: var(--title-grey);
    margin-top: 19px; line-height: 34px;
  }
  .category-link {
    text-align: center; font-size: 14px; color: var(--accent-brown); margin-top: 7px; line-height: 20px;
  }
  .nature { left: 111px; top: 770px; }
  .nature .category-photo { height: 427px; background: linear-gradient(160deg, #8a7160, #c4ab95 45%, #a38672 70%, #6b5646); }
  .animals { left: 645px; top: 700px; }
  .animals .category-photo { height: 592px; background: linear-gradient(180deg, #b8d8a8 0%, #2f5560 20%, #2c2e68 40%, #c9a428 65%, #2d2b5a 88%, #8a7560 100%); }
  .architecture { left: 111px; top: 1480px; }
  .architecture .category-photo { height: 592px; background: linear-gradient(180deg, #e6e8ea 0%, #b9a896 25%, #9a5a3f 50%, #8c5a45 75%, #cfcac3 100%); }
  .weddings { left: 645px; top: 1550px; }
  .weddings .category-photo { height: 427px; background: radial-gradient(ellipse at 55% 45%, #2a2c3f 0%, #4a4850 25%, #9c9488 55%, #c3b9a4 100%); }

  .site-footer {
    position: absolute; left: 0; top: 2290px; width: 1200px; height: 121px;
    background: var(--footer-bg); color: var(--footer-text);
    font-family: "Open Sans", sans-serif; font-size: 12px;
  }
  .site-footer span { position: absolute; top: 48px; white-space: nowrap; }
</style>
</head>
<body>
  <header class="hero" role="img" aria-label="Mountain forest above a sea of clouds at sunrise">
    <div class="brand"><span class="brand-dot"></span>Bram Kellet Photography</div>
    <nav class="main-nav">
      <span style="left:0">HOME</span>
      <span style="left:69px">FEATURED PHOTOGRAPHY</span>
      <span style="left:258px">PORTFOLIO</span>
      <span style="left:357px">BIO</span>
      <span style="left:411px">STORE</span>
      <svg class="cart" viewBox="0 0 26 24" fill="none" stroke="#ffffff" stroke-width="1.6" stroke-linejoin="round" stroke-linecap="round">
        <path d="M1 2h4l3 13h13l3-9H7"/>
        <circle cx="10" cy="20" r="1.8"/>
        <circle cx="19" cy="20" r="1.8"/>
      </svg>
      <span class="cart-count">0</span>
    </nav>
    <h1 class="hero-title">BRAM KELLET PHOTOGRAPHY</h1>
    <p class="hero-sub">Sit amet consectetur adipis elit sed consectetur adipis elit sed</p>
  </header>

  <section class="category nature">
    <div class="category-num">01</div>
    <div class="category-photo" role="img" aria-label="Layered sandstone cliff with a small cave"></div>
    <h2 class="category-name">Nature</h2>
    <div class="category-link">SEE MORE</div>
  </section>

  <section class="category animals">
    <div class="category-num">02</div>
    <div class="category-photo" role="img" aria-label="Colourful starling perched on a branch"></div>
    <h2 class="category-name">Animals Portraits</h2>
    <div class="category-link">SEE MORE</div>
  </section>

  <section class="category architecture">
    <div class="category-num">03</div>
    <div class="category-photo" role="img" aria-label="Modern brick and stone campus building"></div>
    <h2 class="category-name">Architecture</h2>
    <div class="category-link">SEE MORE</div>
  </section>

  <section class="category weddings">
    <div class="category-num">04</div>
    <div class="category-photo" role="img" aria-label="Wedding rings resting on granite"></div>
    <h2 class="category-name">Weddings</h2>
    <div class="category-link">SEE MORE</div>
  </section>

  <footer class="site-footer">
    <span style="left:195px">Copyrights ©. 2020 Allrights Reserved.</span>
    <span style="left:694px">Snapline</span>
    <span style="left:826px">Photonest</span>
    <span style="left:961px">Chatterly</span>
  </footer>
</body>
</html>
```